Harrowmere Freight, Project

Company Profile
Harrowmere Freight Sdn Bhd is a well established and experienced freight forwarder in Kuala Lumpur, Malaysia. We specialize in air and sea forwarding, Custom Brokerage and regulatory compliance services, inland transportation,
overseas freighting and warehousing and distribution management. With our dedicated qualified and experienced professionals, we are fully committed to serving our clients.

Our Mission
Based on the motto “Quick, Reliable and Polite”, Harrowmere Freight is dedicated to upholding the following three points corporate philosophy:
1. Adhering to the principle that “the customer always comes first”.
2. Contributing to the development of the local community.
3. Making it our duty to be responsible and sincere.

Our Edge
• One-Stop Logistics Solutions
• Extensive Network Throughout Malaysia
• Highly Qualified and Experienced Pool of Professionals
• Comprehensive IT Solutions
• Innovative and Customer-focused Solutions
• Flexible and Consistent in Managing Exceptions
• Total Supply Chain Visibility

Target Market(s)

We sell the logistics services to all the industry in Malaysia. (ONE Stop Logistics Solutions)

Industry/Entity Type

Logistic

Contact Information for Business Card

I want the back of the card to be white with the logo and slogan. i would like to see the logo on the front with the general info.

Requirements
Must have
• Name, Title, Office, Cell, Fax, Email, Address, Website
Nice to have
• Modern Design Business Card

```html
<!DOCTYPE html>
<html lang="en">
<head>
<meta charset="utf-8">
<title>Harrowmere Freight – Stationery Set</title>
<link href="https://fonts.googleapis.com/css2?family=Open+Sans:wght@600&family=Roboto:wght@400;500&display=swap" rel="stylesheet">
<style>
  :root {
    --ink: #2e2e2e;
    --band-dark: #333333;
    --blue-a: #2e5dab;
    --blue-b: #4b9dcb;
    --brand: #2c5ba8;
    --text: #1f1f1f;
    --paper: #ffffff;
    --muted: #4a4a4a;
  }
  * { box-sizing: border-box; margin: 0; padding: 0; }
  html, body { width: 1200px; height: 1200px; overflow: hidden; background: var(--paper); }
  body { position: relative; font-family: "Roboto", sans-serif; color: var(--text); }

  .sheet { position: absolute; background: var(--paper); box-shadow: 0 1px 6px rgba(0,0,0,0.18); overflow: hidden; }
  .sheet svg.shape { position: absolute; left: 0; top: 0; width: 100%; height: 100%; }

  .slogan { position: absolute; left: 0; width: 100%; text-align: center; color: #fff;
            font-family: "Open Sans", sans-serif; font-weight: 600; }

  .brand-name { position: absolute; font-family: "Roboto", sans-serif; font-weight: 500; color: var(--brand); line-height: 1.05; }

  .company { position: absolute; left: 0; width: 100%; text-align: center; color: #fff; font-weight: 500; }
  .address { position: absolute; left: 0; width: 100%; text-align: center; color: #fff; }

  .contact { position: absolute; font-size: 7.2px; line-height: 1; color: var(--text); }
  .contact li { list-style: none; display: flex; align-items: center; gap: 4px; height: 11.6px; }
  .contact .icon { width: 7px; height: 7px; border-radius: 1px; background: var(--brand); flex: none; }
  .contact b { font-weight: 500; color: var(--brand); }

  /* presentation folder */
  .folder { left: 52px; top: 48px; width: 528px; height: 742px; }
  .folder .slogan { top: 26px; font-size: 11px; }
  .folder .brand-name { left: 0; width: 100%; text-align: center; top: 168px; font-size: 24px; }
  .folder .company { top: 690px; font-size: 11px; }
  .folder .address { top: 712px; font-size: 6.8px; }

  /* letterhead */
  .letterhead { left: 622px; top: 48px; width: 527px; height: 742px; }
  .letterhead .slogan { top: 15px; font-size: 12px; }
  .letterhead .brand-name { left: 78px; top: 112px; font-size: 16px; }
  .letterhead .contact { left: 345px; top: 87px; }
  .letterhead .company { top: 684px; font-size: 12px; }
  .letterhead .address { top: 707px; font-size: 7.6px; }

  /* envelope back */
  .envelope-back { left: 327px; top: 894px; width: 506px; height: 259px; }

  /* envelope front */
  .envelope { left: 52px; top: 817px; width: 506px; height: 257px; }
  .envelope .slogan { top: 10px; font-size: 10px; }
  .envelope .brand-name { left: 16px; top: 74px; font-size: 12px; }
  .envelope .contact { left: 392px; top: 50px; }
  .envelope .company { top: 222px; font-size: 9.5px; }
  .envelope .address { top: 238px; font-size: 6px; }

  /* business card back */
  .card-back { left: 878px; top: 817px; width: 271px; height: 153px; }
  .card-back .slogan { top: 8px; font-size: 7px; }
  .card-back .heading { position: absolute; top: 41px; width: 100%; text-align: center; color: #fff; font-size: 8px; letter-spacing: 0.2px; }
  .card-back .rule { position: absolute; top: 65px; left: 111px; width: 50px; height: 1px; background: rgba(255,255,255,0.7); }
  .card-back .services { position: absolute; top: 80px; width: 100%; text-align: center; color: #fff; font-size: 7px; line-height: 9px; }

  /* business card front */
  .card-front { left: 878px; top: 998px; width: 271px; height: 154px; }
  .card-front .brand-name { left: 20px; top: 62px; font-size: 15px; }
  .card-front .person { position: absolute; left: 139px; top: 20px; }
  .card-front .person h2 { font-size: 8px; font-weight: 500; text-transform: uppercase; color: var(--ink); }
  .card-front .person p { font-size: 6.8px; color: var(--muted); margin-top: 1px; }
  .card-front .contact { left: 139px; font-size: 5.8px; }
  .card-front .contact li { height: 9.5px; gap: 3px; }
  .card-front .contact .icon { width: 5.5px; height: 5.5px; }
  .card-front .company { top: 128px; font-size: 6px; }
  .card-front .address { top: 138px; font-size: 3.6px; }
</style>
</head>
<body>
<svg width="0" height="0" style="position:absolute">
  <defs>
    <linearGradient id="brandBlue" x1="0" y1="0" x2="1" y2="1">
      <stop offset="0" stop-color="#2e5dab"/>
      <stop offset="1" stop-color="#4b9dcb"/>
    </linearGradient>
  </defs>
</svg>

<!-- presentation folder -->
<section class="sheet folder">
  <svg class="shape" viewBox="0 0 528 742" preserveAspectRatio="none">
    <path d="M0 0H528V24Q264 72 0 24Z" fill="#333"/>
    <path d="M0 224Q264 192 528 224V742H0Z" fill="url(#brandBlue)"/>
  </svg>
  <p class="slogan">ONE STOP LOGISTICS SOLUTIONS</p>
  <p class="brand-name">Harrowmere Freight</p>
  <p class="company">HARROWMERE FREIGHT SDN. BHD. (1204388-X)</p>
  <p class="address">No. 8B, 2nd Floor, Jalan Seri Kenanga 3, Taman Kenanga Jaya, 41050 Klang, Selangor Darul Ehsan, Malaysia.</p>
</section>

<!-- letterhead -->
<section class="sheet letterhead">
  <svg class="shape" viewBox="0 0 527 742" preserveAspectRatio="none">
    <path d="M0 0H527V20Q263 62 0 20Z" fill="#333"/>
    <path d="M0 692Q263 648 527 692V742H0Z" fill="url(#brandBlue)"/>
  </svg>
  <p class="slogan">ONE STOP LOGISTICS SOLUTIONS</p>
  <p class="brand-name">Harrowmere Freight</p>
  <ul class="contact">
    <li><span class="icon"></span>+ (603) 3250 1180 / 1190</li>
    <li><span class="icon"></span>+ (603) 3250 1195</li>
    <li><span class="icon"></span>www.<b>harrowmere</b>.com.my</li>
  </ul>
  <p class="company">HARROWMERE FREIGHT SDN. BHD. (1204388-X)</p>
  <p class="address">No. 8B, 2nd Floor, Jalan Seri Kenanga 3, Taman Kenanga Jaya, 41050 Klang, Selangor Darul Ehsan, Malaysia.</p>
</section>

<!-- envelope back -->
<section class="sheet envelope-back">
  <svg class="shape" viewBox="0 0 506 259" preserveAspectRatio="none">
    <path d="M0 0H506V66Q250 70 0 80Z" fill="url(#brandBlue)"/>
  </svg>
</section>

<!-- envelope front -->
<section class="sheet envelope">
  <svg class="shape" viewBox="0 0 506 257" preserveAspectRatio="none">
    <path d="M0 0H506V19Q253 52 0 19Z" fill="#333"/>
    <path d="M0 227Q253 198 506 227V257H0Z" fill="url(#brandBlue)"/>
  </svg>
  <p class="slogan">ONE STOP LOGISTICS SOLUTIONS</p>
  <p class="brand-name">Harrowmere Freight</p>
  <ul class="contact">
    <li><span class="icon"></span>+ (603) 3250 1180 / 1190</li>
    <li><span class="icon"></span>+ (603) 3250 1195</li>
    <li><span class="icon"></span>www.<b>harrowmere</b>.com.my</li>
  </ul>
  <p class="company">HARROWMERE FREIGHT SDN. BHD. (1204388-X)</p>
  <p class="address">No. 8B, 2nd Floor, Jalan Seri Kenanga 3, Taman Kenanga Jaya, 41050 Klang, Selangor Darul Ehsan, Malaysia.</p>
</section>

<!-- business card back -->
<section class="sheet card-back">
  <svg class="shape" viewBox="0 0 271 153" preserveAspectRatio="none">
    <rect width="271" height="153" fill="url(#brandBlue)"/>
    <path d="M0 0H271V7Q135 38 0 7Z" fill="#333"/>
  </svg>
  <p class="slogan">ONE STOP LOGISTICS SOLUTIONS</p>
  <p class="heading">WE'RE SPECIALIZE IN</p>
  <span class="rule"></span>
  <p class="services">
    · International Shipping (Air / Sea) · Transportation / Haulage<br>
    · Consolidation – NVOCC · Project Management<br>
    · Packing · Supply Chain Management · Warehousing<br>
    · Marine Insurance · Tax Exemption Consultancy · Distribution<br>
    · Customs Brokerage · Door to Door
  </p>
</section>

<!-- business card front -->
<section class="sheet card-front">
  <svg class="shape" viewBox="0 0 271 154" preserveAspectRatio="none">
    <path d="M0 130Q135 106 271 130V154H0Z" fill="url(#brandBlue)"/>
  </svg>
  <p class="brand-name">Harrowmere<br>Freight</p>
  <div class="person">
    <h2>Aminuddin Rahman</h2>
    <p>Managing Director</p>
  </div>
  <ul class="contact" style="top:43px">
    <li><span class="icon"></span>+6012-418 2275</li>
  </ul>
  <ul class="contact" style="top:58px">
    <li><span class="icon"></span>+ (603) 3250 1180 / 1190</li>
    <li><span class="icon"></span>+ (603) 3250 1195</li>
  </ul>
  <ul class="contact" style="top:86px">
    <li><span class="icon"></span>aminuddin.r@<b>harrowmere</b>.com.my</li>
    <li><span class="icon"></span>www.<b>harrowmere</b>.com.my</li>
  </ul>
  <p class="company">HARROWMERE FREIGHT SDN. BHD. (1204388-X)</p>
  <p class="address">No. 8B, 2nd Floor, Jalan Seri Kenanga 3, Taman Kenanga Jaya, 41050 Klang, Selangor Darul Ehsan, Malaysia.</p>
</section>
</body>
</html>
```